business card for a massage therapy practice named 'Cedar and Willow Massage Studio'

I really need a trendy, yet easy on the eyes business card to complement my logo. Ideally with some gold or rose gold foil work.

My uploaded file of the logo I have in horizontal but I have a vertical version as well. Another color that is used in the website is a blush pink here and there. I'd like to see some trendy tropical leaves in the design.

```html
<!DOCTYPE html>
<html lang="en">
<head>
<meta charset="utf-8">
<title>Cedar and Willow Massage Studio — Business Card</title>
<link href="https://fonts.googleapis.com/css2?family=Roboto:wght@400&display=swap" rel="stylesheet">
<style>
  :root {
    --backdrop: #efeeea;
    --card: #fbfaf8;
    --foil: #c2976a;
    --foil-light: #e3c9a6;
    --foil-deep: #b0835a;
    --card-shadow: rgba(60, 50, 40, 0.12);
  }
  * { margin: 0; padding: 0; box-sizing: border-box; }
  html, body {
    width: 966px; height: 1200px; overflow: hidden;
    background: var(--backdrop);
    font-family: "Roboto", Arial, sans-serif;
    color: var(--foil);
  }
  .canvas { position: relative; width: 966px; height: 1200px; }
  .card {
    position: absolute; left: 193px; width: 580px; height: 340px;
    background: var(--card);
    box-shadow: 0 6px 22px var(--card-shadow);
    overflow: hidden;
  }
  .card--front { top: 140px; }
  .card--back { top: 780px; }

  .palm-fronds {
    position: absolute; right: 0; top: 0; width: 340px; height: 300px;
    background: radial-gradient(ellipse at 85% 10%, var(--foil-light) 0%, var(--foil) 35%, rgba(194,151,106,0.45) 60%, rgba(194,151,106,0) 78%);
  }
  .holder { position: absolute; left: 32px; top: 184px; }
  .holder__name { font-size: 26px; line-height: 1.1; }
  .holder__license { font-size: 14px; letter-spacing: 1px; margin-top: 2px; }
  .contact {
    position: absolute; left: 32px; top: 255px;
    display: flex; align-items: flex-end; font-size: 14.5px; line-height: 19px;
  }
  .contact__lines { padding-right: 12px; }
  .contact__address { border-left: 1.5px solid var(--foil); padding-left: 14px; margin-top: 16px; }

  .brand {
    position: absolute; left: 0; right: 0; top: 95px;
    display: flex; align-items: center; justify-content: center; gap: 18px;
  }
  .brand__mark { width: 46px; height: 46px; border-radius: 50%; background: var(--foil); flex: none; }
  .brand__name { font-size: 36px; line-height: 1.1; }
  .brand__tagline { font-size: 17px; letter-spacing: 5px; margin-top: 6px; }
  .social { position: absolute; left: 0; right: 0; top: 272px; display: flex; justify-content: center; gap: 5px; }
  .social__dot { width: 18px; height: 18px; border-radius: 50%; background: var(--foil); }
  .handle { position: absolute; left: 0; right: 0; top: 302px; text-align: center; font-size: 13px; letter-spacing: 2.5px; }
</style>
</head>
<body>
<main class="canvas">
  <section class="card card--front" aria-label="Card front">
    <div class="palm-fronds" role="img" aria-label="Gold foil tropical palm fronds in the top right corner"></div>
    <div class="holder">
      <p class="holder__name">Marisol Lindqvist</p>
      <p class="holder__license">LMT #48215</p>
    </div>
    <div class="contact">
      <div class="contact__lines">
        <p>(916) 555-0148</p>
        <p>info@cedarandwillow.com</p>
        <p>www.cedarandwillow.com</p>
      </div>
      <div class="contact__address">
        <p>2140 Oak Row #210</p>
        <p>Sacramento, CA 95816</p>
      </div>
    </div>
  </section>

  <section class="card card--back" aria-label="Card back">
    <div class="brand">
      <span class="brand__mark" aria-hidden="true"></span>
      <div>
        <p class="brand__name">Cedar and Willow</p>
        <p class="brand__tagline">MASSAGE STUDIO</p>
      </div>
    </div>
    <div class="social" aria-label="Social media links">
      <span class="social__dot"></span><span class="social__dot"></span><span class="social__dot"></span><span class="social__dot"></span><span class="social__dot"></span>
    </div>
    <p class="handle">@CEDARANDWILLOW</p>
  </section>
</main>
</body>
</html>
```